Wren of Fabrics relaunch: brand, logo and website redesign

Wren of Fabrics www.wrenoffabrics.com is relaunching to focus on empowering style advice, e books and courses.
We need a new logo, brand identity and website which reflects this change.
The structure of the site and pages have been completed http://dev1.wrenoffabrics.com/
but we need to update the brand look and feel
Please read the full brief, uploaded, before submitting your designs.

Target Market(s)

Women, primarily aged 28-45, English speaking USA and UK
Ambitious and determined. Looking for solutions. Open to self-improvement.
Maybe not as confident with style and body image as other parts of their life.

Logo Text

Brand name Wren of Fabrics Strapline version 1: Unlock your personal best Strapline version 2: Unlock better Logo/graphical icon for use with/without text

Number of Pages Required

3 page

Font styles to use
Sans Serif

Requirements
Must have
• 1. Web designs for home page, a channel page and advice page (see attached brief)
Web designs must be consistent with new website design navigation, and page structure http://dev1.wrenoffabrics.com/
2. Web style guide to include colour palettes/system; web fonts, icons, illustrations and guidelines/examples free stock photography. see Mindmap upload for example of colour pallette we like.
Nice to have
• Ebook front covers
Quiz promotions
Course promotions
Other web pages
Social media pages eg Pagebook, Snapgrid,Chirpline
Should not have
• Paid photography or photos where don’t have the rights

```html
<!DOCTYPE html>
<html lang="en">
<head>
<meta charset="utf-8">
<title>Wren of Fabrics</title>
<link href="https://fonts.googleapis.com/css2?family=Rajdhani:wght@500;600;700&family=Satisfy&family=Arimo:wght@400;700&display=swap" rel="stylesheet">
<style>
:root{
  --orange:#f07b2a;
  --orange-soft:#f5b27c;
  --lime:#a3d521;
  --ink:#222222;
  --body:#555555;
  --line:#e6e6e6;
  --footer:#1e1e1e;
  --white:#ffffff;
}
*{margin:0;padding:0;box-sizing:border-box}
html,body{width:1200px;height:4563px;overflow:hidden;background:var(--white)}
body{position:relative;font-family:"Arimo",Arial,sans-serif;color:var(--body)}
.abs{position:absolute}
.heading{font-family:"Rajdhani",sans-serif;font-weight:600;color:var(--ink);letter-spacing:.5px;white-space:nowrap;line-height:1.1}
.script{font-family:"Satisfy",cursive;color:var(--orange);font-weight:400;white-space:nowrap;line-height:1.2}
.btn{position:absolute;display:flex;align-items:center;justify-content:center;border-radius:30px;font-family:"Rajdhani",sans-serif;font-weight:600;font-size:16px;color:var(--white);letter-spacing:.5px;background:var(--orange);white-space:nowrap}
.btn--lime{background:var(--lime)}
.center{left:0;width:1200px;text-align:center}

/* header */
.site-header{top:0;left:0;width:1200px;height:129px;background:var(--white)}
.brand-mark{left:112px;top:24px;width:50px;height:80px;border-radius:50%;background:var(--orange)}
.brand-name{left:172px;top:28px;font-family:"Rajdhani",sans-serif;font-weight:600;font-size:34px;color:#333;white-space:nowrap;line-height:1.1}
.brand-line{left:216px;top:72px;font-size:13px;color:var(--orange);white-space:nowrap}
.nav{top:58px;font-family:"Rajdhani",sans-serif;font-weight:700;font-size:14px;color:#333;white-space:nowrap}
.nav--active{color:var(--orange)}
.icon-ring{top:38px;width:56px;height:56px;border-radius:50%;border:2px solid var(--orange);display:flex;align-items:center;justify-content:center}
.icon-ring--lime{border-color:var(--lime)}

/* hero */
.hero-photo{top:129px;left:0;width:1200px;height:700px;background:linear-gradient(100deg,#6f8fb0 0%,#c9cfd4 40%,#ecebe6 65%,#e7d9d4 100%)}
.hero-title{left:762px;top:270px;font-size:48px}
.hero-sub{left:764px;top:332px;font-size:30px}

/* about */
.about-ring{left:156px;top:976px;width:450px;height:450px;border-radius:50%;border:6px solid var(--orange-soft)}
.about-photo{left:250px;top:910px;width:270px;height:510px;border-radius:130px 130px 20px 20px;background:linear-gradient(180deg,#d9d6d2 0%,#2c3f8e 40%,#1f2d6e 100%)}
.about-title{left:670px;top:958px;font-size:38px}
.about-name{left:665px;top:1005px;font-size:32px}
.about-text{left:666px;top:1085px;width:420px;font-size:13.5px;line-height:26px;text-align:justify}
.about-text p+p{margin-top:26px}

/* courses */
.courses-band{top:1520px;left:0;width:1200px;height:432px;background:linear-gradient(90deg,#ee8a2c 0%,#e99a1e 35%,#c3c91f 65%,#a6d521 100%)}
.courses-script{top:1557px;font-size:40px;color:var(--white)}
.courses-title{top:1620px;font-size:40px;color:var(--white)}
.courses-sub{top:1680px;font-size:15px;color:var(--white);white-space:nowrap}
.video-frame{left:197px;top:1745px;width:806px;height:457px;background:var(--white);padding:6px}
.video-still{width:100%;height:100%;background:linear-gradient(90deg,#8d7a6e 0%,#c9a28e 35%,#b9b0a8 60%,#e7a8a0 80%,#f06a2a 100%)}
.play{left:550px;top:1924px}

/* advice */
.advice-title{top:2250px;font-size:36px}
.advice-script{top:2297px;font-size:32px}
.card{position:absolute;top:2377px;width:312px;height:518px;background:var(--white);border:1px solid var(--line);border-radius:6px;box-shadow:0 2px 6px rgba(0,0,0,.08);overflow:hidden;text-align:center}
.card-image{height:245px}
.card-title{margin-top:30px;font-size:22px}
.card-rule{width:34px;height:2px;background:var(--orange);margin:14px auto 18px}
.card-text{padding:0 26px;font-size:13px;line-height:27px}
.card .btn{left:81px;top:430px;width:150px;height:50px}
.dots{top:2924px;left:574px;display:flex;gap:5px}
.dot{width:13px;height:13px;border-radius:50%;background:#888}
.dot--on{background:var(--orange)}

/* ebooks */
.ebooks-band{top:2985px;left:0;width:1200px;height:521px;background:var(--orange)}
.ebooks-title{left:112px;top:3072px;font-size:38px;color:var(--white)}
.ebooks-script{left:110px;top:3120px;font-size:32px;color:var(--white)}
.ebooks-text{left:112px;top:3188px;width:520px;font-size:13px;line-height:26px;color:var(--white)}
.book-cover{left:741px;top:3029px;width:336px;height:452px;background:linear-gradient(180deg,#3a3a3a 0%,#6a6a6a 45%,#e8c33a 75%,#b8222f 100%);box-shadow:6px 6px 12px rgba(0,0,0,.3)}

/* quizzes */
.quiz-title{top:3557px;font-size:36px}
.quiz-script{top:3603px;font-size:32px}
.quiz-card{position:absolute;top:3703px;width:473px;height:230px;background:var(--white);border:1px solid var(--line);box-shadow:0 2px 6px rgba(0,0,0,.08);border-radius:4px;overflow:hidden}
.quiz-image{position:absolute;left:0;top:0;width:195px;height:230px}
.quiz-name{position:absolute;left:215px;top:28px;font-size:23px}
.quiz-text{position:absolute;left:215px;top:76px;width:238px;font-size:13px;line-height:25px}
.quiz-card .btn{left:215px;top:166px;width:126px;height:42px;font-family:"Arimo",sans-serif;font-weight:400;font-size:14px}

/* social strip */
.strip{top:4023px;left:0;width:1200px;height:270px;display:flex}
.strip-tile{flex:1}
.strip-label{top:4088px;font-family:"Rajdhani",sans-serif;font-weight:700;font-size:110px;line-height:1.1;color:var(--white);white-space:nowrap}

/* footer */
.site-footer{top:4293px;left:0;width:1200px;height:270px;background:var(--footer)}
.footer-nav{top:4364px;left:0;width:1200px;display:flex;justify-content:center}
.footer-nav span{font-family:"Rajdhani",sans-serif;font-weight:600;font-size:15px;color:var(--white);padding:0 32px;white-space:nowrap}
.socials{top:4418px;left:496px;display:flex;gap:8px}
.social{width:36px;height:36px;border-radius:50%;border:2px solid var(--white)}
.copyright{top:4488px;font-size:12px;color:var(--white)}
</style>
</head>
<body>

<header class="site-header abs">
  <div class="brand-mark abs"></div>
  <div class="brand-name abs">Wren of Fabrics</div>
  <div class="brand-line abs">Unlock your personal best</div>
  <span class="nav nav--active abs" style="left:454px">HOME</span>
  <span class="nav abs" style="left:521px">ABOUT</span>
  <span class="nav abs" style="left:592px">ADVICE</span>
  <span class="nav abs" style="left:670px">COURSES</span>
  <span class="nav abs" style="left:759px">QUIZZES</span>
  <span class="nav abs" style="left:844px">EBOOKS</span>
  <span class="nav abs" style="left:925px">BLOG</span>
  <div class="icon-ring abs" style="left:966px">
    <svg width="20" height="18" viewBox="0 0 20 18"><path d="M1 2h3l3 9h9l2-6H6" fill="none" stroke="#f07b2a" stroke-width="2"/><circle cx="8" cy="15" r="1.6" fill="#f07b2a"/><circle cx="15" cy="15" r="1.6" fill="#f07b2a"/></svg>
  </div>
  <div class="icon-ring icon-ring--lime abs" style="left:1030px">
    <svg width="18" height="18" viewBox="0 0 18 18"><circle cx="7.5" cy="7.5" r="5" fill="none" stroke="#a3d521" stroke-width="2.2"/><path d="M11 11l5 5" stroke="#a3d521" stroke-width="2.4"/></svg>
  </div>
</header>

<section>
  <div class="hero-photo abs" role="img" aria-label="Stylist fitting a blouse on a client in a studio with dress forms"></div>
  <h1 class="hero-title heading abs">NEW COURSE</h1>
  <div class="hero-sub script abs">How to Organise Your Wardrobe</div>
  <a class="btn" style="left:762px;top:399px;width:168px;height:55px">LEARN MORE</a>
</section>

<section>
  <div class="about-ring abs"></div>
  <div class="about-photo abs" role="img" aria-label="Portrait of stylist Helena Marsh in a blue blouse"></div>
  <h2 class="about-title heading abs">ABOUT</h2>
  <div class="about-name script abs">Helena Marsh</div>
  <div class="about-text abs">
    <p>Helena Marsh's clean cut, figure flattering and empowering dresses reflect contemporary classics and the latest trends. Helena fuses impeccable tailoring and chic styling to create timeless and elegant dresses for every occasion. Made in the UK with luxurious Italian fabrics.</p>
    <p>Helena's innovative online boutique, makes it easy to find unique, elegant styles designed to flatter your body shape.</p>
  </div>
  <a class="btn" style="left:668px;top:1323px;width:175px;height:59px">READ MORE</a>
</section>

<section>
  <div class="courses-band abs"></div>
  <div class="courses-script script abs center">Wren of Fabrics</div>
  <h2 class="courses-title heading abs center">COURSES</h2>
  <p class="courses-sub abs center">Sed ut perspiciatis unde omnis iste natus error sit voluptatem accusantium doloremque laudantium</p>
  <div class="video-frame abs"><div class="video-still" role="img" aria-label="Course video still of the stylist speaking beside a clothes rail"></div></div>
  <svg class="play abs" width="100" height="100" viewBox="0 0 100 100"><circle cx="50" cy="50" r="47" fill="rgba(0,0,0,.35)" stroke="#fff" stroke-width="4"/><path d="M40 30v40l32-20z" fill="#fff"/></svg>
</section>

<section>
  <h2 class="advice-title heading abs center">STYLE ADVICE</h2>
  <div class="advice-script script abs center">What &amp; How To Wear</div>

  <article class="card" style="left:112px">
    <div class="card-image" role="img" aria-label="Hands holding a colour swatch fan over fashion sketches" style="background:linear-gradient(120deg,#b89a7a,#e7d6c4 50%,#e46a5a 70%,#f2f0ee)"></div>
    <h3 class="card-title heading">COLOUR GUIDES</h3>
    <div class="card-rule"></div>
    <p class="card-text">Colour is individual, natural, magnetic, influential, emotional, therapeutic and part of a woman's beauty and charm.</p>
    <a class="btn">LEARN MORE</a>
  </article>

  <article class="card" style="left:443px">
    <div class="card-image" role="img" aria-label="Close-up of blue and orange checked fabric" style="background:linear-gradient(135deg,#1d3f8a,#4a72c0 45%,#e0663a 60%,#2b4d9e)"></div>
    <h3 class="card-title heading">SHAPE GUIDES</h3>
    <div class="card-rule"></div>
    <p class="card-text">The clothes which will flatter you best will depend on your body shape. Today the choice of clothes is so varied</p>
    <a class="btn btn--lime">LEARN MORE</a>
  </article>

  <article class="card" style="left:776px">
    <div class="card-image" role="img" aria-label="Designer measuring a dress form in front of sketch boards" style="background:linear-gradient(90deg,#7d7d7d,#dcdcdc 45%,#f3f1ef)"></div>
    <h3 class="card-title heading">MEASUREMENT GUIDES</h3>
    <div class="card-rule"></div>
    <p class="card-text">The following guidelines should help you to measure yourself in order to find your perfect size in the UK or when buying</p>
    <a class="btn">LEARN MORE</a>
  </article>

  <div class="dots abs"><span class="dot"></span><span class="dot dot--on"></span><span class="dot"></span></div>
</section>

<section>
  <div class="ebooks-band abs"></div>
  <h2 class="ebooks-title heading abs">EBOOKS</h2>
  <div class="ebooks-script script abs">Sed ut perspiciatis unde</div>
  <p class="ebooks-text abs">Nemo enim ipsam voluptatem quia voluptas sit aspernatur aut odit aut fugit, sed quia consequuntur magni dolores eos qui ratione voluptatem sequi nesciunt. Neque porro quisquam est, qui dolorem ipsum quia dolor sit amet, consectetur, adipisci velit, sed quia non numquam eius modi tempora incidunt ut labore et dolore magnam aliquam quaerat voluptatem. Ut enim ad minima veniam, quis nostrum exercitationem ullam corporis suscipit laboriosam, nisi ut aliquid ex ea commodi consequatur</p>
  <a class="btn btn--lime" style="left:112px;top:3362px;width:170px;height:58px">LEARN MORE</a>
  <div class="book-cover abs" role="img" aria-label="Ebook cover: personal stylist guide with author portrait and clothes rail"></div>
</section>

<section>
  <h2 class="quiz-title heading abs center">QUIZZES</h2>
  <div class="quiz-script script abs center">Discover Your Style DNA</div>

  <article class="quiz-card" style="left:112px">
    <div class="quiz-image" role="img" aria-label="Sketchbook with a fashion illustration and pencil" style="background:linear-gradient(135deg,#eeeeee,#d8d8d8 60%,#b4477a)"></div>
    <h3 class="quiz-name heading">STYLE QUIZ</h3>
    <p class="quiz-text">Take the fast and fun style discover your unique style DNA. Free guides to for your body shape and age.</p>
    <a class="btn">Read More</a>
  </article>

  <article class="quiz-card" style="left:615px">
    <div class="quiz-image" role="img" aria-label="Bridal bouquet of pink and white roses" style="background:linear-gradient(135deg,#e9d8c8,#d9849a 50%,#6b8a4a)"></div>
    <h3 class="quiz-name heading">WEDDING QUIZ</h3>
    <p class="quiz-text">Take the fast and fun style discover your unique style DNA. Free guides to for your body shape and age.</p>
    <a class="btn">Read More</a>
  </article>
</section>

<section>
  <div class="strip abs" role="img" aria-label="Row of social feed photos: lake at dusk, chimneys, grasses, street mural, old truck">
    <div class="strip-tile" style="background:linear-gradient(#6a4a6e,#2a1f2a)"></div>
    <div class="strip-tile" style="background:linear-gradient(#2f7cc4,#b5522e)"></div>
    <div class="strip-tile" style="background:linear-gradient(#5c7fa8,#a69a52)"></div>
    <div class="strip-tile" style="background:linear-gradient(#9aa3ad,#c99a2a)"></div>
    <div class="strip-tile" style="background:linear-gradient(#8a8a8a,#3a3a3a)"></div>
  </div>
  <div class="strip-label abs center">Snapgrid</div>
</section>

<footer>
  <div class="site-footer abs"></div>
  <nav class="footer-nav abs">
    <span>ABOUT</span><span>STYLE ADVICE</span><span>COURSES</span><span>QUIZZES</span><span>EBOOKS</span><span>BLOG</span>
  </nav>
  <div class="socials abs">
    <span class="social"></span><span class="social"></span><span class="social"></span><span class="social"></span><span class="social"></span>
  </div>
  <p class="copyright abs center">© Copyright 2020 Wren of Fabrics.All Rights Reserved</p>
</footer>

</body>
</html>
```